Business Card Design - Amberfield Court

We are looking at a new design for our business cards that has a modern and professional look. We run a residential aged care facility focussing on the care of residents. The cards will be used for potential clients, consultants and business opportunities in this sector. Blue and white is our main colours and would to see these colours incorporated in the design.
Industry/Entity Type
Business
Contact Information for Business Card
Amberfield Court, Darren Walsh, dwalsh@amberfieldcourt.com.au, Finance Manager, 0472 639 208, BCom, 37 Marrabel Crescent, Brindle Vale, Qld 4093.
Look and feel
Each slider illustrates characteristics of the customer's brand and the style your logo design should communicate.

```html
<!DOCTYPE html>
<html lang="en">
<head>
<meta charset="utf-8">
<title>Amberfield Court – Business Card</title>
<link rel="stylesheet" href="https://fonts.googleapis.com/css2?family=Open+Sans:wght@400;600;700&display=swap">
<style>
  :root {
    --backdrop: #2b2b2d;
    --navy: #1f3a4a;
    --navy-accent: #4f7f9c;
    --sky: #00a8e6;
    --white: #ffffff;
    --ink-dark: #1d3543;
  }
  * { box-sizing: border-box; margin: 0; padding: 0; }
  html, body {
    width: 1200px; height: 900px; overflow: hidden;
    background: var(--backdrop);
    font-family: "Open Sans", Arial, sans-serif;
  }
  .canvas {
    width: 1200px; height: 900px;
    display: flex; flex-direction: column; align-items: center; justify-content: center;
    gap: 36px;
  }
  .card {
    width: 700px; height: 400px;
    position: relative;
    box-shadow: 0 14px 30px rgba(0,0,0,0.45);
  }
  .card--front { background: var(--navy); }
  .card--back { background: var(--sky); }

  .brand {
    position: absolute;
    display: flex; flex-direction: column; align-items: center;
  }
  .card--front .brand { left: 50%; top: 50%; transform: translate(-50%, -50%); }
  .card--back .brand { left: 60px; top: 50%; transform: translateY(-50%); width: 300px; }

  .brand__dot {
    width: 110px; height: 110px; border-radius: 50%;
    margin-bottom: 18px;
  }
  .card--front .brand__dot { background: var(--navy-accent); }
  .card--back .brand__dot { background: var(--white); }

  .brand__name {
    font-weight: 600; font-size: 30px; letter-spacing: 2px;
    text-transform: uppercase; color: var(--white);
    line-height: 1; white-space: nowrap;
  }
  .card--back .brand__name { font-size: 24px; }

  .contact {
    position: absolute; left: 400px; top: 110px;
    color: var(--white);
  }
  .contact__name {
    font-weight: 700; font-size: 26px; letter-spacing: 0.5px;
    text-transform: uppercase; line-height: 1.1;
  }
  .contact__role {
    font-size: 13px; text-transform: uppercase; color: var(--ink-dark);
    margin-bottom: 16px;
  }
  .contact__address, .contact__line { font-size: 15px; line-height: 1.5; }
  .contact__address { margin-bottom: 14px; }
  .contact__line { display: flex; align-items: center; gap: 8px; white-space: nowrap; }
  .contact__line svg { width: 13px; height: 13px; fill: var(--white); flex: none; }
</style>
</head>
<body>
<main class="canvas">
  <section class="card card--front" aria-label="Card front">
    <div class="brand">
      <span class="brand__dot"></span>
      <span class="brand__name">Amberfield Court</span>
    </div>
  </section>

  <section class="card card--back" aria-label="Card back">
    <div class="brand">
      <span class="brand__dot"></span>
      <span class="brand__name">Amberfield Court</span>
    </div>
    <div class="contact">
      <p class="contact__name">Darren Walsh</p>
      <p class="contact__role">Finance Manager (BCom)</p>
      <p class="contact__address">37 Marrabel Crescent<br>Brindle Vale, Qld 4093</p>
      <p class="contact__line">
        <svg viewBox="0 0 24 24" aria-hidden="true"><path d="M6.6 10.8a15.1 15.1 0 0 0 6.6 6.6l2.2-2.2a1 1 0 0 1 1-.25 11.4 11.4 0 0 0 3.6.57 1 1 0 0 1 1 1V20a1 1 0 0 1-1 1A17 17 0 0 1 3 4a1 1 0 0 1 1-1h3.5a1 1 0 0 1 1 1c0 1.25.2 2.450.57 3.57a1 1 0 0 1-.25 1z"/></svg>
        0472 639 208
      </p>
      <p class="contact__line">
        <svg viewBox="0 0 24 24" aria-hidden="true"><path d="M2 5h20v14H2zm2 2v.5l8 5 8-5V7zm0 2.8V17h16V9.8l-8 5z"/></svg>
        dwalsh@amberfieldcourt.com.au
      </p>
    </div>
  </section>
</main>
</body>
</html>
```